Lotstallmart.com Webpage Design

Design Brief for lotstallmart.com (Copy of Brief also in attached Word file)

Name of Website- lotstallmart.com (existing logo and look & feel of website to be changed)

Logo - Finalised. The logo files are attached with the brief as “logo.jpeg”. The “Blue- Grey” version of the logo is for use on lighter backgrounds and the “Orange-White” version of the logo is for use on darker backgrounds. (A full Black version of the logo is also attached). Both versions may be used in different parts of the website. All attached files are in .png format.
Status - The website in functional and is undergoing user trials. However, we want to improve the look & feel of the website so at it seems
a. cotemporary,
b. Easy to Navigate
c. professional and
d. Vibrant.

Please visit ‘lotstallmart.com’ to check out the website and its functionalities – please use it only as a reference for the features & functions to be provided, however the designer should use a ‘Free Hand’ in designing the composition of various parts of the webpage without getting too influenced by the existing design

Objective of the Website ‘lotstallmart.com –
a. It is a portal focussed on listing of ‘Retail’ specific real-estate properties by developers, owners and realty brokers. The properties shall listed under the following four categories-
i. Retail Malls
ii. Shopping Complexes
iii. High-street shops
iv. Retail Warehouses
*refer lotstallmart.com for better clarity

b. The abovementioned properties shall be listed either for ‘Sale’ or ‘rent\lease’ or both

c. Users shall visit the site in case they wish to acquire a retail \ shop space either on ‘sale’ or ‘rent’. These Users would be able to specify the ‘Search Criteria’ through the tool-bars provided on the website – the ‘Search Criteria’ shall comprise of ‘Type of space category’, ‘City’, ‘Locality’, transaction type ie ‘Rent \ Sale’ and ‘Area Range’

d. The main revenue model for the website shall be listing fee ( or advertising charges ) payable by those listing their properties on the website.

Three Main Pages of Website (lotstallmart.com) that need to be designed -
a. Main Home Page (visit the web link - http://lotstallmart.com/ ) - The main home page has the “Search Toolbar” for specifying of Search Criteria by the User. It shall also have the following features & functions-
i. Main Advertising Banner
ii. Featured Projects
iii. New Launches
iv. Toolbar with buttons – ‘Advertise with Us’, ‘Listings Alert’, ‘Mart Wizards’, ‘Advertiser Login’

b. Property Listings Page (visit the web link - http://lotstallmart.com/gurgaon-in-india ) - The List of property options that match the Criteria specified by the ‘User’ get displayed on this page.

c. Property Detail Page - When the ‘User’ clicks on the “More….” Button on the ‘Property Listings Page’ (given in point b. above) the web page with the details of the property opens. (For Example – visit the web link - http://lotstallmart.com/vorne-Shopping-Complex-vorne-quadrion-gurgaon-636 )

Note:- Please refer to attached ‘Shopping’ related images the designer may use them on the website to provide a look & feel of retail if required – either separately or rotate in a single window

Target Market(s)

Retailers & Investors looking for retail space, Real Estate Brokers, Developers

Industry/Entity Type

Advertising

Number of Pages Required

3 page

Requirements
Must have
• Refer to existing site lotstallmart.com -- all the existing functionalities are a must have.
Nice to have
• The Designer may use the retail related images on the website if required for making it more vibrant. Refer attached images Shopping(1-6).jpg

```html
<!DOCTYPE html>
<html lang="en">
<head>
<meta charset="utf-8">
<title>Lotstallmart.com – Home</title>
<link rel="stylesheet" href="https://fonts.googleapis.com/css2?family=Open+Sans:wght@300;400;600;700&display=swap">
<style>
:root{
  --blue:#0a9bf0;
  --blue-deep:#0b5fa8;
  --blue-field:#0d6fc0;
  --grey-tab:#6b6c70;
  --grey-btn:#6e6f73;
  --footer:#6d6e71;
  --ink:#222;
  --muted:#555;
  --white:#fff;
  --dark:#2c2d30;
}
*{box-sizing:border-box;margin:0;padding:0}
html,body{width:1200px;height:2326px;overflow:hidden;background:#fff}
body{position:relative;font-family:"Open Sans",Arial,sans-serif;color:var(--ink)}
.abs{position:absolute}

/* header */
.site-header{left:0;top:0;width:1200px;height:110px;background:#fff}
.brand{left:52px;top:26px;display:flex;align-items:center;gap:10px}
.brand-dot{width:44px;height:44px;border-radius:50%;background:var(--blue)}
.brand-name{font-size:34px;font-weight:700;color:var(--blue-deep);letter-spacing:-.5px}
.top-nav{left:524px;top:46px;font-size:13px;color:#222;display:flex;gap:8px}
.login-btn{left:858px;top:40px;width:128px;height:32px;background:#4a4b4e;color:#fff;font-size:12.5px;display:flex;align-items:center;justify-content:center;border-radius:2px}
.city-select{left:1010px;top:40px;width:135px;height:32px;border:1px solid #555;font-size:12.5px;display:flex;align-items:center;justify-content:space-between;padding:0 10px}

/* hero */
.hero{left:0;top:110px;width:1200px;height:440px;background:radial-gradient(ellipse at 50% 40%,#8a7458 0%,#4b3a2c 45%,#1e1813 100%)}
.hero-title{left:0;top:240px;width:1200px;text-align:center;font-size:58px;font-weight:300;color:#fff;letter-spacing:-.5px}
.hero-btn{left:515px;top:340px;width:171px;height:40px;background:var(--blue);color:#fff;font-size:12.5px;font-weight:600;letter-spacing:1px;display:flex;align-items:center;justify-content:center}
.hero-arrow{top:322px;color:#fff;font-size:20px}

/* search */
.search{left:51px;top:597px;width:1098px;height:158px;background:var(--blue);border-radius:4px 4px 0 0;overflow:hidden}
.search-tabs{height:32px;background:var(--grey-tab);display:flex;align-items:center;padding-left:20px;gap:0}
.tab{display:flex;align-items:center;gap:9px;color:#fff;font-size:12px;font-weight:600;letter-spacing:.6px;width:220px}
.tab:before{content:"";width:14px;height:14px;background:#3b3c3f}
.field-label{top:57px;font-size:13px;color:#fff}
.field{top:88px;height:42px;background:var(--blue-field);color:#fff;font-size:12px;display:flex;align-items:center;justify-content:space-between;padding:0 12px}
.field.text{background:#fff0;border:1px solid #cfe9fb;background:var(--blue-field)}
.search-btn{left:949px;top:86px;width:131px;height:42px;background:var(--blue-deep);color:#fff;font-size:13px;font-weight:600;letter-spacing:1px;display:flex;align-items:center;justify-content:center}

/* sections */
.section-title{left:51px;font-size:23px;font-weight:400;letter-spacing:2px;color:#111}
.project-photo{width:240px;height:178px}
.project-note{font-size:11.5px;color:#333;display:flex;align-items:center;gap:8px;width:260px;white-space:nowrap}
.city-tag{width:93px;height:36px;background:var(--blue);color:#fff;font-size:17px;display:flex;align-items:center;justify-content:center}
.view-btn{width:95px;height:36px;background:var(--grey-btn);color:#fff;font-size:17px;display:flex;align-items:center;justify-content:center}
.launch{width:319px;height:197px}
.launch-bar{position:absolute;left:0;bottom:0;width:100%;height:38px;background:rgba(35,35,38,.8);color:#fff;font-size:16px;display:flex;align-items:center;padding-left:7px}
.launch-bar .zoom{position:absolute;right:0;top:0;width:38px;height:38px;border-left:1px solid #999;display:flex;align-items:center;justify-content:center}

/* footer */
.site-footer{left:0;top:2048px;width:1200px;height:278px;background:var(--footer);color:#fff}
.footer-brand{left:84px;top:28px;display:flex;align-items:center;gap:10px}
.footer-brand .brand-dot{background:#fff;width:40px;height:40px}
.footer-brand .brand-name{color:#fff;font-size:30px}
.footer-links{left:81px;font-size:12.5px;display:flex;gap:8px}
.offer-title{left:748px;top:24px;font-size:16.5px;font-weight:600}
.email-box{left:750px;top:80px;width:181px;height:38px;background:#f2f2f2;color:#444;font-size:12.5px;display:flex;align-items:center;padding-left:11px;border-radius:4px 0 0 4px}
.signup-btn{left:930px;top:80px;width:82px;height:38px;background:#2a2a2c;color:#fff;font-size:12.5px;display:flex;align-items:center;justify-content:center;border-radius:0 4px 4px 0}
.phone{left:798px;top:136px;font-size:23px;font-weight:600;letter-spacing:1px}
.footer-rule{left:81px;top:195px;width:1038px;height:1px;background:#858689}
.copyright{left:87px;top:218px;font-size:12.5px}
.social{top:210px;width:38px;height:38px;border:1.5px solid #ddd;border-radius:50%}
</style>
</head>
<body>

<header class="abs site-header">
  <div class="abs brand"><span class="brand-dot"></span><span class="brand-name">lotstallmart</span></div>
  <nav class="abs top-nav"><span>Advertise with Us</span><span>|</span><span>Listings Alert</span><span>|</span><span>Mart Wizards</span></nav>
  <div class="abs login-btn">Advertiser Login</div>
  <div class="abs city-select"><span>Select City</span>
    <svg width="10" height="6" viewBox="0 0 10 6"><path d="M1 1l4 4 4-4" stroke="#333" fill="none" stroke-width="1.5"/></svg></div>
</header>

<section class="abs hero" role="img" aria-label="Family walking with shopping bags through a lit shopping arcade">
</section>
<div class="abs hero-title">The City at Your Doorstep</div>
<div class="abs hero-btn">FIND OUT MORE</div>
<div class="abs hero-arrow" style="left:8px">‹</div>
<div class="abs hero-arrow" style="left:1182px">›</div>

<form class="abs search">
  <div class="search-tabs">
    <span class="tab">RETAIL MALLS</span>
    <span class="tab">SHOPPING COMPLEX</span>
    <span class="tab">HIGH STREET SHOPS</span>
    <span class="tab">RETAIL WAREHOUSES</span>
  </div>
  <span class="abs field-label" style="left:20px">Sale Or Rent Or Both</span>
  <span class="abs field-label" style="left:252px">Select City</span>
  <span class="abs field-label" style="left:484px">Select Locality/Micro-Market</span>
  <span class="abs field-label" style="left:718px">Enter Keywords</span>
  <div class="abs field" style="left:17px;width:200px"><span>Both</span><svg width="10" height="6"><path d="M1 1l4 4 4-4" stroke="#fff" fill="none" stroke-width="1.5"/></svg></div>
  <div class="abs field" style="left:249px;width:196px"><span>select</span><svg width="10" height="6"><path d="M1 1l4 4 4-4" stroke="#fff" fill="none" stroke-width="1.5"/></svg></div>
  <div class="abs field" style="left:482px;width:195px"><span>select</span><svg width="10" height="6"><path d="M1 1l4 4 4-4" stroke="#fff" fill="none" stroke-width="1.5"/></svg></div>
  <div class="abs field text" style="left:713px;width:197px"><span>name of project, Developer etc</span></div>
  <div class="abs search-btn">SEARCH</div>
</form>

<h2 class="abs section-title" style="top:810px">FEATURED PROJECTS</h2>

<!-- featured row 1 -->
<div class="abs project-photo" style="left:51px;top:872px;background:linear-gradient(135deg,#cfc6bd,#6d5a4c)" role="img" aria-label="Two women with shopping bags on an escalator"></div>
<div class="abs project-photo" style="left:335px;top:872px;background:linear-gradient(135deg,#e6b84a,#a63a2f)" role="img" aria-label="Family shopping near a sale window"></div>
<div class="abs project-photo" style="left:624px;top:872px;background:linear-gradient(135deg,#eae6d8,#d2862e)" role="img" aria-label="Woman carrying colourful bags in a mall"></div>
<div class="abs project-photo" style="left:908px;top:872px;background:linear-gradient(135deg,#c9b8b0,#3d4a6a)" role="img" aria-label="Couple resting with shopping bags"></div>

<!-- featured row 2 -->
<div class="abs project-photo" style="left:51px;top:1189px;background:linear-gradient(135deg,#eeeef0,#c85c8a)" role="img" aria-label="Woman holding many shopping bags"></div>
<div class="abs project-photo" style="left:335px;top:1189px;background:linear-gradient(135deg,#f2d59a,#b8403c)" role="img" aria-label="Two friends shopping together"></div>
<div class="abs project-photo" style="left:624px;top:1189px;background:linear-gradient(135deg,#e9e7e2,#5c5a54)" role="img" aria-label="Woman with shopping bags in a store"></div>
<div class="abs project-photo" style="left:908px;top:1189px;background:linear-gradient(135deg,#c6b39a,#a9344f)" role="img" aria-label="Two women walking with shopping bags"></div>

<!-- notes and buttons -->
<div class="abs project-note" style="left:51px;top:1061px"><svg width="9" height="13" viewBox="0 0 9 13"><path d="M4.5 0A4.5 4.5 0 0 0 0 4.5C0 8 4.5 13 4.5 13S9 8 9 4.5A4.5 4.5 0 0 0 4.5 0zm0 6.3a1.8 1.8 0 1 1 0-3.6 1.8 1.8 0 0 1 0 3.6z" fill="#222"/></svg>Lorem Ipsum. Proin gravida nibh vel</div>
<div class="abs project-note" style="left:335px;top:1061px"><svg width="9" height="13" viewBox="0 0 9 13"><path d="M4.5 0A4.5 4.5 0 0 0 0 4.5C0 8 4.5 13 4.5 13S9 8 9 4.5A4.5 4.5 0 0 0 4.5 0zm0 6.3a1.8 1.8 0 1 1 0-3.6 1.8 1.8 0 0 1 0 3.6z" fill="#222"/></svg>Lorem Ipsum. Proin gravida nibh vel</div>
<div class="abs project-note" style="left:624px;top:1061px"><svg width="9" height="13" viewBox="0 0 9 13"><path d="M4.5 0A4.5 4.5 0 0 0 0 4.5C0 8 4.5 13 4.5 13S9 8 9 4.5A4.5 4.5 0 0 0 4.5 0zm0 6.3a1.8 1.8 0 1 1 0-3.6 1.8 1.8 0 0 1 0 3.6z" fill="#222"/></svg>Lorem Ipsum. Proin gravida nibh vel</div>
<div class="abs project-note" style="left:908px;top:1061px"><svg width="9" height="13" viewBox="0 0 9 13"><path d="M4.5 0A4.5 4.5 0 0 0 0 4.5C0 8 4.5 13 4.5 13S9 8 9 4.5A4.5 4.5 0 0 0 4.5 0zm0 6.3a1.8 1.8 0 1 1 0-3.6 1.8 1.8 0 0 1 0 3.6z" fill="#222"/></svg>Lorem Ipsum. Proin gravida nibh vel</div>
<div class="abs project-note" style="left:51px;top:1378px"><svg width="9" height="13" viewBox="0 0 9 13"><path d="M4.5 0A4.5 4.5 0 0 0 0 4.5C0 8 4.5 13 4.5 13S9 8 9 4.5A4.5 4.5 0 0 0 4.5 0zm0 6.3a1.8 1.8 0 1 1 0-3.6 1.8 1.8 0 0 1 0 3.6z" fill="#222"/></svg>Lorem Ipsum. Proin gravida nibh vel</div>
<div class="abs project-note" style="left:335px;top:1378px"><svg width="9" height="13" viewBox="0 0 9 13"><path d="M4.5 0A4.5 4.5 0 0 0 0 4.5C0 8 4.5 13 4.5 13S9 8 9 4.5A4.5 4.5 0 0 0 4.5 0zm0 6.3a1.8 1.8 0 1 1 0-3.6 1.8 1.8 0 0 1 0 3.6z" fill="#222"/></svg>Lorem Ipsum. Proin gravida nibh vel</div>
<div class="abs project-note" style="left:624px;top:1378px"><svg width="9" height="13" viewBox="0 0 9 13"><path d="M4.5 0A4.5 4.5 0 0 0 0 4.5C0 8 4.5 13 4.5 13S9 8 9 4.5A4.5 4.5 0 0 0 4.5 0zm0 6.3a1.8 1.8 0 1 1 0-3.6 1.8 1.8 0 0 1 0 3.6z" fill="#222"/></svg>Lorem Ipsum. Proin gravida nibh vel</div>
<div class="abs project-note" style="left:908px;top:1378px"><svg width="9" height="13" viewBox="0 0 9 13"><path d="M4.5 0A4.5 4.5 0 0 0 0 4.5C0 8 4.5 13 4.5 13S9 8 9 4.5A4.5 4.5 0 0 0 4.5 0zm0 6.3a1.8 1.8 0 1 1 0-3.6 1.8 1.8 0 0 1 0 3.6z" fill="#222"/></svg>Lorem Ipsum. Proin gravida nibh vel</div>

<div class="abs city-tag" style="left:51px;top:1093px">Gurgaon</div><div class="abs view-btn" style="left:147px;top:1093px">View List</div>
<div class="abs city-tag" style="left:335px;top:1093px">Noida</div><div class="abs view-btn" style="left:431px;top:1093px">View List</div>
<div class="abs city-tag" style="left:624px;top:1093px">Mohali</div><div class="abs view-btn" style="left:720px;top:1093px">View List</div>
<div class="abs city-tag" style="left:908px;top:1093px">Gurgaon</div><div class="abs view-btn" style="left:1004px;top:1093px">View List</div>
<div class="abs city-tag" style="left:51px;top:1410px">Gurgaon</div><div class="abs view-btn" style="left:147px;top:1410px">View List</div>
<div class="abs city-tag" style="left:335px;top:1410px">Gurgaon</div><div class="abs view-btn" style="left:431px;top:1410px">View List</div>
<div class="abs city-tag" style="left:624px;top:1410px">Gurgaon</div><div class="abs view-btn" style="left:720px;top:1410px">View List</div>
<div class="abs city-tag" style="left:908px;top:1410px">Gurgaon</div><div class="abs view-btn" style="left:1004px;top:1410px">View List</div>

<h2 class="abs section-title" style="top:1502px">NEW LAUNCHES</h2>

<div class="abs launch" style="left:51px;top:1568px;background:linear-gradient(135deg,#d9cbb9,#7c5d4a)" role="img" aria-label="Group of friends shopping in Bhopal">
  <div class="launch-bar">Bhopal<span class="zoom"><svg width="16" height="16" viewBox="0 0 16 16"><circle cx="10" cy="6" r="4.5" stroke="#2aa2f0" stroke-width="2" fill="none"/><path d="M6.8 9.2L2 14" stroke="#2aa2f0" stroke-width="2.5"/></svg></span></div></div>
<div class="abs launch" style="left:440px;top:1568px;background:linear-gradient(135deg,#eef0dc,#8fa05a)" role="img" aria-label="Mother and child in a bright mall corridor in Mohali">
  <div class="launch-bar">Mohali<span class="zoom"><svg width="16" height="16" viewBox="0 0 16 16"><circle cx="10" cy="6" r="4.5" stroke="#2aa2f0" stroke-width="2" fill="none"/><path d="M6.8 9.2L2 14" stroke="#2aa2f0" stroke-width="2.5"/></svg></span></div></div>
<div class="abs launch" style="left:829px;top:1568px;background:linear-gradient(135deg,#e2cdb8,#a5554a)" role="img" aria-label="Smiling couple shopping in Chennai">
  <div class="launch-bar">Chennai<span class="zoom"><svg width="16" height="16" viewBox="0 0 16 16"><circle cx="10" cy="6" r="4.5" stroke="#2aa2f0" stroke-width="2" fill="none"/><path d="M6.8 9.2L2 14" stroke="#2aa2f0" stroke-width="2.5"/></svg></span></div></div>
<div class="abs launch" style="left:51px;top:1789px;background:linear-gradient(135deg,#e4d8c6,#b44a6a)" role="img" aria-label="Family with shopping bags in a Noida store">
  <div class="launch-bar">Noida<span class="zoom"><svg width="16" height="16" viewBox="0 0 16 16"><circle cx="10" cy="6" r="4.5" stroke="#2aa2f0" stroke-width="2" fill="none"/><path d="M6.8 9.2L2 14" stroke="#2aa2f0" stroke-width="2.5"/></svg></span></div></div>
<div class="abs launch" style="left:440px;top:1789px;background:linear-gradient(135deg,#e9e3dc,#8a7466)" role="img" aria-label="Three friends shopping in New Delhi">
  <div class="launch-bar">New Delhi<span class="zoom"><svg width="16" height="16" viewBox="0 0 16 16"><circle cx="10" cy="6" r="4.5" stroke="#2aa2f0" stroke-width="2" fill="none"/><path d="M6.8 9.2L2 14" stroke="#2aa2f0" stroke-width="2.5"/></svg></span></div></div>
<div class="abs launch" style="left:829px;top:1789px;background:linear-gradient(135deg,#7fa3c8,#b0466a)" role="img" aria-label="Shoppers browsing clothing racks in Gurgaon">
  <div class="launch-bar">Gurgaon<span class="zoom"><svg width="16" height="16" viewBox="0 0 16 16"><circle cx="10" cy="6" r="4.5" stroke="#2aa2f0" stroke-width="2" fill="none"/><path d="M6.8 9.2L2 14" stroke="#2aa2f0" stroke-width="2.5"/></svg></span></div></div>

<footer class="abs site-footer">
  <div class="abs footer-brand"><span class="brand-dot"></span><span class="brand-name">lotstallmart</span></div>
  <nav class="abs footer-links" style="top:121px"><span>Retail Malls</span><span>|</span><span>Shopping Complex</span><span>|</span><span>High Street Shops</span><span>|</span><span>Retail Warehouses</span></nav>
  <nav class="abs footer-links" style="top:148px"><span>About Us</span><span>|</span><span>Privacy Policy</span><span>|</span><span>Terms of Use</span><span>|</span><span>Contact Us</span><span>|</span><span>Site Map</span></nav>
  <div class="abs offer-title">Don’t Miss Our Exclusive Offers</div>
  <div class="abs email-box">enter your email here</div>
  <div class="abs signup-btn">SIGNUP</div>
  <div class="abs phone">+91 200 555 0147</div>
  <div class="abs footer-rule"></div>
  <div class="abs copyright">Copyright 2014 lotstallmart. All rights reserved</div>
  <span class="abs social" style="left:777px"></span>
  <span class="abs social" style="left:825px"></span>
  <span class="abs social" style="left:873px"></span>
  <span class="abs social" style="left:921px"></span>
  <span class="abs social" style="left:969px"></span>
</footer>

</body>
</html>
```